Design a website for a newly developed Delta 8 THC Company

Design a responsive Website with the following goals in mind:
- Built on Wordpress/WooCommerce theme. Please use this when designing for ease of integration.
- Build trust with website visitors with an engaging, informative content driven website, that leads to a conversion of product purchase and repeat business. We will also be driving consumers to businesses that carry our products as well.
- The website will embody a lifestyle feel and make the visitor identify with the content.
- The website will allow for super charged SEO and other digital marketing and advertising strategies and tactics used to increase discovery, awareness, and conversion.
Please see additional goals in the uploaded files.
Target Market(s)
Male/Female 21-
Industry/Entity Type
Cannabis/Hemp
Coding
Coded - Design and coding required
Number of Pages Required
5+ page
Font styles to use
Other font styles liked:
- Montserrat
Look and feel
Each slider illustrates characteristics of the customer's brand and the style your logo design should communicate.

```html
<!DOCTYPE html>
<html lang="en">
<head>
<meta charset="utf-8">
<title>Aurelis — Delta 8</title>
<link href="https://fonts.googleapis.com/css2?family=Montserrat:wght@400;500;600;700;800&family=Cormorant+Garamond:wght@400&family=Arimo:wght@400&display=swap" rel="stylesheet">
<style>
:root{
  --black:#0b0b0b;
  --brown:#7a4e22;
  --brown-dark:#6b4524;
  --gold:#c99a3d;
  --gold-light:#d9b063;
  --band:#c9a043;
  --grey-bg:#f3f3f3;
  --dark:#222326;
  --text:#444;
  --white:#fff;
  --btn:linear-gradient(90deg,#85561f 0%,#d2a659 50%,#8a5b24 100%);
}
*{margin:0;padding:0;box-sizing:border-box}
html,body{width:1200px;height:3935px;overflow:hidden}
body{position:relative;font-family:'Montserrat',sans-serif;background:var(--white);color:var(--text)}
.abs{position:absolute}
a{color:inherit;text-decoration:none}

/* header */
.site-header{left:0;top:0;width:1200px;height:140px;background:var(--black)}
.header-rule{left:0;top:140px;width:1200px;height:6px;background:linear-gradient(90deg,#9b6a2c,#e0b66a,#9b6a2c)}
.brand{font-family:'Cormorant Garamond',serif;font-weight:400;color:var(--gold);line-height:1;white-space:nowrap}
.site-header .brand{left:110px;top:48px;font-size:44px;letter-spacing:14px}
.main-nav a{position:absolute;top:66px;font-size:14px;font-weight:600;color:var(--white)}
.main-nav a.active{color:var(--gold)}
.cart{left:1032px;top:47px;width:56px;height:56px;border:2px solid var(--gold);border-radius:50%;color:var(--gold);font-size:13px;text-align:center;padding-top:8px;line-height:1}

/* hero */
.hero{left:0;top:146px;width:1200px;height:790px;overflow:hidden}
.hero-bg{position:absolute;inset:0;background:radial-gradient(ellipse at 40% 30%,#2e4a25 0%,#15240f 45%,#070a06 100%)}
.hero-title{left:105px;top:232px;font-size:104px;font-weight:800;color:var(--gold);letter-spacing:2px;line-height:1}
.hero-sub{left:112px;top:341px;font-size:33px;font-weight:600;color:var(--white);line-height:49px}
.btn{display:block;background:var(--btn);color:var(--white);font-weight:500;text-align:center;border-radius:32px}
.hero .btn{left:114px;top:460px;width:179px;height:61px;line-height:61px;font-size:17px}
.hero-product{left:712px;top:200px;width:480px;height:560px;border-radius:40px;background:radial-gradient(ellipse at 45% 55%,#5a3410 0%,#2a1a0a 55%,rgba(20,14,8,0) 80%)}

/* section titles */
.section-title{width:1200px;left:0;text-align:center;font-size:36px;font-weight:700;color:var(--brown)}
.section-title span{color:var(--gold)}
.title-rule{left:577px;width:46px;height:3px;background:var(--brown)}

/* welcome */
.welcome-text{left:226px;top:1070px;width:748px;text-align:center;font-family:'Arimo',sans-serif;font-size:15px;line-height:28.5px;color:var(--text)}
.welcome .btn{left:502px;top:1243px;width:196px;height:62px;line-height:62px;font-size:17px}

/* products */
.products-band{left:0;top:1362px;width:1200px;height:605px;background:var(--grey-bg)}
.card{width:235px;height:388px;background:var(--white);border:1px solid #e6e6e6;box-shadow:0 0 4px rgba(0,0,0,.06)}
.card-media{position:absolute;left:8px;top:7px;width:218px;height:240px;background:linear-gradient(160deg,#fafafa,#e9e9e9)}
.card-media .bottle{position:absolute;left:58px;top:18px;width:60px;height:205px;border-radius:22px 22px 10px 10px;background:linear-gradient(90deg,#1a0e05,#6a3e12 45%,#1a0e05)}
.card-media .fruit{position:absolute;left:106px;top:120px;width:90px;height:95px;border-radius:45%}
.card-name{position:absolute;top:260px;width:100%;text-align:center;font-size:17px;font-weight:600;color:var(--brown)}
.card-price{position:absolute;top:294px;left:36px;font-size:19px;font-weight:500;color:var(--gold)}
.card-stars{position:absolute;top:297px;left:113px;font-size:14px;letter-spacing:1px;color:#e3ac1d}
.card-actions{position:absolute;top:335px;left:63px;display:flex;gap:8px}
.icon-btn{width:32px;height:32px;border-radius:50%;border:1px solid #ccc;display:flex;align-items:center;justify-content:center;background:var(--white)}
.icon-btn.solid{background:var(--brown);border-color:var(--brown)}

/* benefits */
.benefits{left:0;top:1967px;width:1200px;height:589px;background:radial-gradient(ellipse at 50% 40%,#34353a,#1c1d20)}
.benefits .section-title{top:55px;color:var(--white)}
.benefits .title-rule{top:106px;background:var(--gold)}
.benefit{font-family:'Arimo',sans-serif;font-size:15px;line-height:26px;color:#e6e6e6;width:270px}
.benefit .tick{position:absolute;top:5px}
.benefit.left{padding-left:40px}
.benefit.left .tick{left:0}
.benefit.right{text-align:right}
.benefit.right .tick{right:-48px}
.benefit-visual{left:404px;top:158px;width:392px;height:392px;border:2px solid var(--gold);border-radius:50%}
.benefit-visual .disc{position:absolute;left:18px;top:18px;width:352px;height:352px;border-radius:50%;background:#d0a345}
.benefit-visual .bottle{position:absolute;left:132px;top:-30px;width:126px;height:420px;border-radius:40px 40px 20px 20px;background:linear-gradient(90deg,#1a0e05,#6a3e12 45%,#1a0e05)}

/* newsletter */
.newsletter{left:0;top:3160px;width:1200px;height:380px;background:radial-gradient(ellipse at 50% 40%,#cfa84c,#c49a3c)}
.newsletter .section-title{top:60px;color:var(--white)}
.newsletter .title-rule{top:114px;background:var(--white)}
.newsletter-sub{left:0;top:130px;width:1200px;text-align:center;font-family:'Arimo',sans-serif;font-size:17px;color:var(--white)}
.email-field{left:188px;top:183px;width:824px;height:60px;border-radius:30px;background:var(--white);padding-left:24px;line-height:60px;font-family:'Arimo',sans-serif;font-size:17px;color:#333}
.subscribe{left:501px;top:263px;width:199px;height:59px;line-height:59px;border-radius:30px;background:var(--brown-dark);color:var(--white);text-align:center;font-size:16px;font-weight:500}

/* footer */
.site-footer{left:0;top:3540px;width:1200px;height:395px;background:var(--black);color:#eee}
.site-footer .brand{left:165px;top:110px;font-size:40px;letter-spacing:12px}
.divider{width:1px;height:120px;top:72px;background:#444}
.contact{font-family:'Arimo',sans-serif;font-size:15px;line-height:22.5px;color:#eee}
.social{width:42px;height:42px;border:2px solid #fff;border-radius:50%}
.footer-rule{left:112px;top:252px;width:978px;height:1px;background:#333}
.footer-nav a{position:absolute;top:292px;font-size:15px;font-weight:600;color:var(--white)}
.footer-nav a.active{color:var(--gold)}
.copyright{left:0;top:340px;width:1200px;text-align:center;font-family:'Arimo',sans-serif;font-size:17px;color:#eee}
</style>
</head>
<body>

<header class="abs site-header">
  <div class="abs brand">AURELIS</div>
  <nav class="main-nav">
    <a class="active" href="#" style="left:473px">HOME</a>
    <a href="#" style="left:569px">ABOUT US</a>
    <a href="#" style="left:697px">PRODUCTS</a>
    <a href="#" style="left:830px">BLOG</a>
    <a href="#" style="left:922px">CONTACT US</a>
  </nav>
  <div class="abs cart">0<br>
    <svg width="16" height="14" viewBox="0 0 16 14"><path d="M1 1h3l2 8h7l2-6H5" fill="none" stroke="#c99a3d" stroke-width="1.8"/><circle cx="7" cy="12" r="1.3" fill="#c99a3d"/><circle cx="12" cy="12" r="1.3" fill="#c99a3d"/></svg>
  </div>
</header>
<div class="abs header-rule"></div>

<section class="abs hero">
  <div class="hero-bg" role="img" aria-label="Close-up of dark green hemp leaves"></div>
  <svg class="abs" style="left:0;top:0" width="1200" height="790" viewBox="0 0 1200 790">
    <path d="M0 720 C120 790 260 790 420 730 C620 650 760 560 930 600 C1050 628 1130 680 1200 720 L1200 790 L0 790 Z" fill="#fff"/>
    <path d="M0 720 C120 790 260 790 420 730 C620 650 760 560 930 600 C1050 628 1130 680 1200 720" fill="none" stroke="#a3742f" stroke-width="6"/>
  </svg>
  <div class="abs hero-product" role="img" aria-label="Two amber dropper bottles of Delta-8 gummies with colourful gummy bears"></div>
  <h1 class="abs hero-title">DELTA 8</h1>
  <p class="abs hero-sub">THC COMPANY WORKING IN THE<br>CANNABIS/HEMP INDUSTRY</p>
  <a class="abs btn" href="#">SHOP NOW</a>
</section>

<section class="welcome">
  <h2 class="abs section-title" style="top:988px">WELCOME TO <span>DELTA 8</span></h2>
  <div class="abs title-rule" style="top:1044px"></div>
  <p class="abs welcome-text">Sed ut perspiciatis unde omnis iste natus error sit voluptatem accusantium doloremque laudantium, totam rem aperiam, eaque ipsa quae ab illo inventore veritatis et quasi architecto beatae vitae dicta sunt explicabo. Nemo enim ipsam voluptatem quia voluptas sit aspernatur aut odit aut fugit, sed quia consequuntur magni dolores eos qui ratione voluptatem sequi nesciunt. Neque porro quisquam est, qui dolorem ipsum quia dolor incidunt ut labore et dolore magnam aliquam quaerat voluptatem.</p>
  <a class="abs btn" href="#">READ MORE</a>
</section>

<div class="abs products-band"></div>
<h2 class="abs section-title" style="top:1410px">FEATURED <span>PRODUCT</span></h2>
<div class="abs title-rule" style="top:1466px"></div>

<article class="abs card" style="left:110px;top:1515px">
  <div class="card-media" role="img" aria-label="Dropper bottle with gummy bears"><div class="bottle"></div><div class="fruit" style="background:#e8742c"></div></div>
  <div class="card-name">PRODUCT NAME</div><div class="card-price">$24.00</div><div class="card-stars">★★★★★</div>
  <div class="card-actions"><span class="icon-btn solid"><svg width="14" height="12"><path d="M1 1h2l2 7h6l2-5H4" fill="none" stroke="#fff" stroke-width="1.6"/></svg></span><span class="icon-btn"><svg width="12" height="12"><circle cx="3" cy="6" r="2" fill="#555"/><circle cx="9" cy="2.5" r="2" fill="#555"/><circle cx="9" cy="9.5" r="2" fill="#555"/><path d="M3 6L9 2.5M3 6l6 3.5" stroke="#555"/></svg></span><span class="icon-btn"><svg width="14" height="10"><ellipse cx="7" cy="5" rx="6" ry="4" fill="none" stroke="#7a4e22" stroke-width="1.4"/><circle cx="7" cy="5" r="1.8" fill="#7a4e22"/></svg></span></div>
</article>
<article class="abs card" style="left:358px;top:1515px">
  <div class="card-media" role="img" aria-label="Dropper bottle with blue raspberries"><div class="bottle"></div><div class="fruit" style="background:#3a4fd8"></div></div>
  <div class="card-name">PRODUCT NAME</div><div class="card-price">$24.00</div><div class="card-stars">★★★★★</div>
  <div class="card-actions"><span class="icon-btn solid"><svg width="14" height="12"><path d="M1 1h2l2 7h6l2-5H4" fill="none" stroke="#fff" stroke-width="1.6"/></svg></span><span class="icon-btn"><svg width="12" height="12"><circle cx="3" cy="6" r="2" fill="#555"/><circle cx="9" cy="2.5" r="2" fill="#555"/><circle cx="9" cy="9.5" r="2" fill="#555"/><path d="M3 6L9 2.5M3 6l6 3.5" stroke="#555"/></svg></span><span class="icon-btn"><svg width="14" height="10"><ellipse cx="7" cy="5" rx="6" ry="4" fill="none" stroke="#7a4e22" stroke-width="1.4"/><circle cx="7" cy="5" r="1.8" fill="#7a4e22"/></svg></span></div>
</article>
<article class="abs card" style="left:606px;top:1515px">
  <div class="card-media" role="img" aria-label="Dropper bottle with cherries"><div class="bottle"></div><div class="fruit" style="background:#6e0f1c"></div></div>
  <div class="card-name">PRODUCT NAME</div><div class="card-price">$24.00</div><div class="card-stars">★★★★★</div>
  <div class="card-actions"><span class="icon-btn solid"><svg width="14" height="12"><path d="M1 1h2l2 7h6l2-5H4" fill="none" stroke="#fff" stroke-width="1.6"/></svg></span><span class="icon-btn"><svg width="12" height="12"><circle cx="3" cy="6" r="2" fill="#555"/><circle cx="9" cy="2.5" r="2" fill="#555"/><circle cx="9" cy="9.5" r="2" fill="#555"/><path d="M3 6L9 2.5M3 6l6 3.5" stroke="#555"/></svg></span><span class="icon-btn"><svg width="14" height="10"><ellipse cx="7" cy="5" rx="6" ry="4" fill="none" stroke="#7a4e22" stroke-width="1.4"/><circle cx="7" cy="5" r="1.8" fill="#7a4e22"/></svg></span></div>
</article>
<article class="abs card" style="left:854px;top:1515px">
  <div class="card-media" role="img" aria-label="Dropper bottle with lemons"><div class="bottle"></div><div class="fruit" style="background:#f1cf3c"></div></div>
  <div class="card-name">PRODUCT NAME</div><div class="card-price">$24.00</div><div class="card-stars">★★★★★</div>
  <div class="card-actions"><span class="icon-btn solid"><svg width="14" height="12"><path d="M1 1h2l2 7h6l2-5H4" fill="none" stroke="#fff" stroke-width="1.6"/></svg></span><span class="icon-btn"><svg width="12" height="12"><circle cx="3" cy="6" r="2" fill="#555"/><circle cx="9" cy="2.5" r="2" fill="#555"/><circle cx="9" cy="9.5" r="2" fill="#555"/><path d="M3 6L9 2.5M3 6l6 3.5" stroke="#555"/></svg></span><span class="icon-btn"><svg width="14" height="10"><ellipse cx="7" cy="5" rx="6" ry="4" fill="none" stroke="#7a4e22" stroke-width="1.4"/><circle cx="7" cy="5" r="1.8" fill="#7a4e22"/></svg></span></div>
</article>

<section class="abs benefits">
  <h2 class="abs section-title">OUR BENEFITS</h2>
  <div class="abs title-rule"></div>
  <div class="abs benefit-visual"><div class="disc"></div><div class="bottle" role="img" aria-label="Amber Delta-8 dropper bottle"></div></div>

  <div class="abs benefit left" style="left:112px;top:190px"><svg class="tick" width="16" height="16"><circle cx="8" cy="8" r="8" fill="#d3a646"/><path d="M4.5 8.3l2.3 2.2 4.5-4.6" fill="none" stroke="#222" stroke-width="1.8"/></svg>Sed ut perspiciatis unde omnis iste natus error sit voluptatem</div>
  <div class="abs benefit left" style="left:112px;top:283px"><svg class="tick" width="16" height="16"><circle cx="8" cy="8" r="8" fill="#d3a646"/><path d="M4.5 8.3l2.3 2.2 4.5-4.6" fill="none" stroke="#222" stroke-width="1.8"/></svg>Sed ut perspiciatis unde omnis iste natus error sit voluptatem</div>
  <div class="abs benefit left" style="left:112px;top:376px"><svg class="tick" width="16" height="16"><circle cx="8" cy="8" r="8" fill="#d3a646"/><path d="M4.5 8.3l2.3 2.2 4.5-4.6" fill="none" stroke="#222" stroke-width="1.8"/></svg>Sed ut perspiciatis unde omnis iste natus error sit voluptatem</div>
  <div class="abs benefit left" style="left:112px;top:469px"><svg class="tick" width="16" height="16"><circle cx="8" cy="8" r="8" fill="#d3a646"/><path d="M4.5 8.3l2.3 2.2 4.5-4.6" fill="none" stroke="#222" stroke-width="1.8"/></svg>Sed ut perspiciatis unde omnis iste natus error sit voluptatem</div>

  <div class="abs benefit right" style="left:778px;top:190px"><svg class="tick" width="16" height="16"><circle cx="8" cy="8" r="8" fill="#d3a646"/><path d="M4.5 8.3l2.3 2.2 4.5-4.6" fill="none" stroke="#222" stroke-width="1.8"/></svg>Sed ut perspiciatis unde omnis iste natus error sit voluptatem</div>
  <div class="abs benefit right" style="left:778px;top:283px"><svg class="tick" width="16" height="16"><circle cx="8" cy="8" r="8" fill="#d3a646"/><path d="M4.5 8.3l2.3 2.2 4.5-4.6" fill="none" stroke="#222" stroke-width="1.8"/></svg>Sed ut perspiciatis unde omnis iste natus error sit voluptatem</div>
  <div class="abs benefit right" style="left:778px;top:376px"><svg class="tick" width="16" height="16"><circle cx="8" cy="8" r="8" fill="#d3a646"/><path d="M4.5 8.3l2.3 2.2 4.5-4.6" fill="none" stroke="#222" stroke-width="1.8"/></svg>Sed ut perspiciatis unde omnis iste natus error sit voluptatem</div>
  <div class="abs benefit right" style="left:778px;top:469px"><svg class="tick" width="16" height="16"><circle cx="8" cy="8" r="8" fill="#d3a646"/><path d="M4.5 8.3l2.3 2.2 4.5-4.6" fill="none" stroke="#222" stroke-width="1.8"/></svg>Sed ut perspiciatis unde omnis iste natus error sit voluptatem</div>
</section>

<h2 class="abs section-title" style="top:2603px">RECENT <span>PRODUCT</span></h2>
<div class="abs title-rule" style="top:2658px"></div>

<article class="abs card" style="left:110px;top:2707px">
  <div class="card-media" role="img" aria-label="Amber dropper bottle"><div class="bottle"></div></div>
  <div class="card-name">PRODUCT NAME</div><div class="card-price">$24.00</div><div class="card-stars">★★★★★</div>
  <div class="card-actions"><span class="icon-btn solid"><svg width="14" height="12"><path d="M1 1h2l2 7h6l2-5H4" fill="none" stroke="#fff" stroke-width="1.6"/></svg></span><span class="icon-btn"><svg width="12" height="12"><circle cx="3" cy="6" r="2" fill="#555"/><circle cx="9" cy="2.5" r="2" fill="#555"/><circle cx="9" cy="9.5" r="2" fill="#555"/><path d="M3 6L9 2.5M3 6l6 3.5" stroke="#555"/></svg></span><span class="icon-btn"><svg width="14" height="10"><ellipse cx="7" cy="5" rx="6" ry="4" fill="none" stroke="#7a4e22" stroke-width="1.4"/><circle cx="7" cy="5" r="1.8" fill="#7a4e22"/></svg></span></div>
</article>
<article class="abs card" style="left:358px;top:2707px">
  <div class="card-media" role="img" aria-label="Amber dropper bottle"><div class="bottle"></div></div>
  <div class="card-name">PRODUCT NAME</div><div class="card-price">$24.00</div><div class="card-stars">★★★★★</div>
  <div class="card-actions"><span class="icon-btn solid"><svg width="14" height="12"><path d="M1 1h2l2 7h6l2-5H4" fill="none" stroke="#fff" stroke-width="1.6"/></svg></span><span class="icon-btn"><svg width="12" height="12"><circle cx="3" cy="6" r="2" fill="#555"/><circle cx="9" cy="2.5" r="2" fill="#555"/><circle cx="9" cy="9.5" r="2" fill="#555"/><path d="M3 6L9 2.5M3 6l6 3.5" stroke="#555"/></svg></span><span class="icon-btn"><svg width="14" height="10"><ellipse cx="7" cy="5" rx="6" ry="4" fill="none" stroke="#7a4e22" stroke-width="1.4"/><circle cx="7" cy="5" r="1.8" fill="#7a4e22"/></svg></span></div>
</article>
<article class="abs card" style="left:606px;top:2707px">
  <div class="card-media" role="img" aria-label="Amber dropper bottle"><div class="bottle"></div></div>
  <div class="card-name">PRODUCT NAME</div><div class="card-price">$24.00</div><div class="card-stars">★★★★★</div>
  <div class="card-actions"><span class="icon-btn solid"><svg width="14" height="12"><path d="M1 1h2l2 7h6l2-5H4" fill="none" stroke="#fff" stroke-width="1.6"/></svg></span><span class="icon-btn"><svg width="12" height="12"><circle cx="3" cy="6" r="2" fill="#555"/><circle cx="9" cy="2.5" r="2" fill="#555"/><circle cx="9" cy="9.5" r="2" fill="#555"/><path d="M3 6L9 2.5M3 6l6 3.5" stroke="#555"/></svg></span><span class="icon-btn"><svg width="14" height="10"><ellipse cx="7" cy="5" rx="6" ry="4" fill="none" stroke="#7a4e22" stroke-width="1.4"/><circle cx="7" cy="5" r="1.8" fill="#7a4e22"/></svg></span></div>
</article>
<article class="abs card" style="left:854px;top:2707px">
  <div class="card-media" role="img" aria-label="Amber dropper bottle"><div class="bottle"></div></div>
  <div class="card-name">PRODUCT NAME</div><div class="card-price">$24.00</div><div class="card-stars">★★★★★</div>
  <div class="card-actions"><span class="icon-btn solid"><svg width="14" height="12"><path d="M1 1h2l2 7h6l2-5H4" fill="none" stroke="#fff" stroke-width="1.6"/></svg></span><span class="icon-btn"><svg width="12" height="12"><circle cx="3" cy="6" r="2" fill="#555"/><circle cx="9" cy="2.5" r="2" fill="#555"/><circle cx="9" cy="9.5" r="2" fill="#555"/><path d="M3 6L9 2.5M3 6l6 3.5" stroke="#555"/></svg></span><span class="icon-btn"><svg width="14" height="10"><ellipse cx="7" cy="5" rx="6" ry="4" fill="none" stroke="#7a4e22" stroke-width="1.4"/><circle cx="7" cy="5" r="1.8" fill="#7a4e22"/></svg></span></div>
</article>

<section class="abs newsletter">
  <h2 class="abs section-title">NEWSLETTER SIGNUP</h2>
  <div class="abs title-rule"></div>
  <p class="abs newsletter-sub">Sed ut perspiciatis unde omnis iste natus error sit voluptatem accusantium doloremque</p>
  <div class="abs email-field">Enter Your Email :</div>
  <div class="abs subscribe">SUBSCRIBE</div>
</section>

<footer class="abs site-footer">
  <div class="abs brand">AURELIS</div>
  <div class="abs divider" style="left:446px"></div>
  <div class="abs divider" style="left:776px"></div>

  <svg class="abs" style="left:490px;top:72px" width="18" height="24" viewBox="0 0 18 24"><path d="M9 1C4.6 1 1.5 4.3 1.5 8.4 1.5 14 9 22.5 9 22.5S16.5 14 16.5 8.4C16.5 4.3 13.4 1 9 1z" fill="none" stroke="#ddd" stroke-width="1.5"/><circle cx="9" cy="8.5" r="2.8" fill="none" stroke="#ddd" stroke-width="1.5"/></svg>
  <div class="abs contact" style="left:530px;top:68px">Address<br>P.O. Box 383 Lorem Ipsum<br>Dummy MA 02471</div>
  <div class="abs social" style="left:530px;top:155px"></div>
  <div class="abs social" style="left:583px;top:155px"></div>

  <svg class="abs" style="left:828px;top:70px" width="22" height="22" viewBox="0 0 22 22"><path d="M5 2l4 4-2.5 2.5c1.2 2.8 3.2 4.8 6 6L15 12l4 4-3 3C9 18 4 13 2 5z" fill="none" stroke="#ddd" stroke-width="1.5"/></svg>
  <div class="abs contact" style="left:868px;top:68px">Phone:<br>000.121.1231</div>
  <svg class="abs" style="left:830px;top:145px" width="22" height="16" viewBox="0 0 22 16"><rect x="1" y="1" width="20" height="14" fill="none" stroke="#ddd" stroke-width="1.5"/><path d="M1 1l10 8 10-8" fill="none" stroke="#ddd" stroke-width="1.5"/></svg>
  <div class="abs contact" style="left:870px;top:136px">Email:<br>info@companyname.com</div>

  <div class="abs footer-rule"></div>
  <nav class="footer-nav">
    <a class="active" href="#" style="left:326px">HOME</a>
    <a href="#" style="left:421px">ABOUT US</a>
    <a href="#" style="left:549px">PRODUCTS</a>
    <a href="#" style="left:683px">BLOG</a>
    <a href="#" style="left:774px">CONTACT US</a>
  </nav>
  <p class="abs copyright">Delta 8 © 2021.All Rights Reserved.</p>
</footer>

</body>
</html>
```